Velmora Freightway Solutions Business cards

Would like a very unique design catchy but professional for business cards. Please use log provided.Marlon WellsCeo and Founder TransCon Logistix Solutions1-888-913-3225mwells@tlsolutionsus.comwww.tlsolutionsus.com

```html
<!DOCTYPE html>
<html lang="en">
<head>
<meta charset="utf-8">
<title>Velmora Freightway Solutions – Business Cards</title>
<link rel="stylesheet" href="https://fonts.googleapis.com/css2?family=Montserrat:wght@600&family=Open+Sans:wght@400;600&display=swap">
<style>
  :root {
    --stage: #1c1c1e;
    --brand-blue: #0b74c1;
    --brand-red: #e3252b;
    --card-white: #ffffff;
    --ink: #222222;
  }
  * { box-sizing: border-box; margin: 0; padding: 0; }
  html, body { width: 1200px; height: 895px; overflow: hidden; }
  body { background: var(--stage); position: relative; font-family: "Open Sans", sans-serif; }

  .card {
    position: absolute;
    width: 620px;
    height: 354px;
    box-shadow: 0 10px 30px rgba(0,0,0,.55);
  }
  .card--back { left: 110px; top: 70px; background: var(--brand-blue); }
  .card--front { left: 470px; top: 470px; background: var(--card-white); }

  .brand-name {
    font-family: "Montserrat", sans-serif;
    font-weight: 600;
    text-transform: uppercase;
    letter-spacing: 3px;
    text-align: center;
    line-height: 1.25;
  }
  .card--back .brand-name {
    position: absolute; left: 0; right: 0; top: 118px;
    color: var(--card-white); font-size: 30px;
  }
  .card--back .brand-web {
    position: absolute; left: 0; right: 0; top: 262px;
    text-align: center; color: var(--card-white);
    font-size: 15px; letter-spacing: 1.5px;
  }

  .card--front .brand-name {
    position: absolute; left: 0; right: 0; top: 52px;
    color: var(--brand-blue); font-size: 24px;
  }
  .person { position: absolute; left: 0; right: 0; top: 148px; text-align: center; }
  .person__name { color: var(--brand-blue); font-size: 38px; font-weight: 600; line-height: 1.1; }
  .person__title { color: var(--ink); font-size: 15px; letter-spacing: .5px; }

  .contact-band {
    position: absolute; left: 0; right: 0; top: 268px; height: 34px;
    background: var(--brand-blue);
    display: flex; align-items: center; justify-content: space-around;
    padding: 0 14px;
  }
  .contact-item { display: flex; align-items: center; gap: 7px; color: var(--card-white); font-size: 15px; }
  .contact-icon { width: 22px; height: 22px; flex: none; }
</style>
</head>
<body>

  <section class="card card--back" aria-label="Card back">
    <p class="brand-name">Velmora Freightway<br>Solutions</p>
    <p class="brand-web">www.vfwayroutes.com</p>
  </section>

  <section class="card card--front" aria-label="Card front">
    <p class="brand-name">Velmora Freightway<br>Solutions</p>
    <div class="person">
      <p class="person__name">Dorian Pike</p>
      <p class="person__title">CEO and Founder</p>
    </div>
    <div class="contact-band">
      <span class="contact-item">
        <svg class="contact-icon" viewBox="0 0 22 22" aria-hidden="true">
          <circle cx="11" cy="11" r="10" fill="var(--brand-red)" stroke="#fff" stroke-width="1.5"/>
          <path d="M7.5 6.5l2 -.5 1 2.5-1.3 1a6 6 0 0 0 2.8 2.8l1-1.3 2.5 1-.5 2c-4 .3-7.8-3.5-7.5-7.5z" fill="#fff"/>
        </svg>
        1-888-470-6158
      </span>
      <span class="contact-item">
        <svg class="contact-icon" viewBox="0 0 22 22" aria-hidden="true">
          <circle cx="11" cy="11" r="10" fill="var(--brand-red)" stroke="#fff" stroke-width="1.5"/>
          <rect x="6" y="7.5" width="10" height="7" fill="#fff"/>
          <path d="M6 7.5l5 4 5-4" fill="none" stroke="var(--brand-red)" stroke-width="1.2"/>
        </svg>
        dpike@vfwayroutes.com
      </span>
      <span class="contact-item">
        <svg class="contact-icon" viewBox="0 0 22 22" aria-hidden="true">
          <circle cx="11" cy="11" r="10" fill="var(--brand-red)" stroke="#fff" stroke-width="1.5"/>
          <g fill="none" stroke="#fff" stroke-width="1.1">
            <circle cx="11" cy="11" r="5"/>
            <ellipse cx="11" cy="11" rx="2.2" ry="5"/>
            <path d="M6 11h10"/>
          </g>
        </svg>
        www.vfwayroutes.com
      </span>
    </div>
  </section>

</body>
</html>
```